SkyvornQ Business Cards and Stationary Design

Need a design for our business cards and stationary. I want to carry on the theme of the logo. I want the business cards to have a design on the back. I would like the business cards and the stationary to carry the same theme, design scheme, and branding

Target Market(s)

Airlines and Maintenance Facilities

Industry/Entity Type

Aviation

Contact Information for Business Card

Name
Position Title
Address: 4827 Trellis Hollow Road, Fort Pierce, Florida, 34951
Office Number
Mobile Number
Email
Website

Font styles to use
Serif
Sans Serif

Colors

Designer to choose colors to be used in the design.

```html
<!DOCTYPE html>
<html lang="en">
<head>
<meta charset="utf-8">
<title>SkyvornQ Business Card</title>
<link rel="stylesheet" href="https://fonts.googleapis.com/css2?family=Ubuntu:wght@400;500;700&display=swap">
<style>
  :root {
    --bg: #e4e4e4;
    --navy: #13395c;
    --blue-deep: #0f4d78;
    --blue-mid: #1f6f9e;
    --sky: #1e8fd6;
    --ink: #1d2f4a;
    --paper: #ffffff;
    --muted: #3a4a60;
  }
  * { box-sizing: border-box; margin: 0; padding: 0; }
  html, body {
    width: 1200px; height: 852px; overflow: hidden;
    background: var(--bg);
    font-family: "Ubuntu", sans-serif;
  }
  .stage {
    position: relative; width: 1200px; height: 852px;
    display: flex; align-items: center; justify-content: center; gap: 40px;
  }
  .card {
    width: 540px; height: 310px; border-radius: 20px;
    position: relative; overflow: hidden;
    box-shadow: 0 6px 14px rgba(0,0,0,0.18);
  }
  .card-back {
    background: linear-gradient(160deg, var(--navy) 0%, var(--blue-deep) 55%, var(--blue-mid) 100%);
  }
  .card-back .wordmark {
    position: absolute; left: 0; right: 0; top: 50%;
    transform: translateY(-50%);
    text-align: center;
    padding-left: 8px;
    color: var(--paper);
    font-weight: 700; font-size: 44px; letter-spacing: 8px;
  }
  .card-front { background: var(--paper); }
  .card-front .wordmark {
    position: absolute; left: 34px; top: 92px;
    color: var(--navy);
    font-weight: 700; font-size: 25px; letter-spacing: 5px;
  }
  .person { position: absolute; left: 34px; top: 146px; }
  .person .name { color: var(--sky); font-weight: 500; font-size: 22px; }
  .person .role { color: var(--muted); font-size: 13px; margin-top: 3px; }
  .contacts {
    position: absolute; left: 34px; top: 204px;
    list-style: none; color: var(--ink); font-size: 13px; line-height: 17px;
  }
  .contacts li { display: flex; align-items: center; gap: 10px; white-space: nowrap; }
  .contacts svg { width: 12px; height: 12px; fill: var(--sky); flex: none; }
  .contacts .address { padding-left: 22px; }
</style>
</head>
<body>
  <main class="stage">
    <section class="card card-back" aria-label="Card back">
      <div class="wordmark">SKYVORNQ</div>
    </section>

    <section class="card card-front" aria-label="Card front">
      <div class="wordmark">SKYVORNQ</div>
      <div class="person">
        <div class="name">Marcus Delvane</div>
        <div class="role">Managing Director</div>
      </div>
      <ul class="contacts">
        <li><svg viewBox="0 0 24 24"><path d="M6.6 10.8a15.1 15.1 0 0 0 6.6 6.6l2.2-2.2c.3-.3.7-.4 1-.2 1.1.4 2.3.6 3.6.6.6 0 1 .4 1 1V20c0 .6-.4 1-1 1A17 17 0 0 1 3 4c0-.6.4-1 1-1h3.5c.6 0 1 .4 1 1 0 1.3.2 2.5.6 3.6.1.3 0 .7-.2 1z"/></svg>5550 2817 436</li>
        <li><svg viewBox="0 0 24 24"><path d="M7 1h10a2 2 0 0 1 2 2v18a2 2 0 0 1-2 2H7a2 2 0 0 1-2-2V3a2 2 0 0 1 2-2zm0 3v14h10V4zm5 15.5a1.2 1.2 0 1 0 0 2.4 1.2 1.2 0 0 0 0-2.4z"/></svg>5550 9362 104</li>
        <li><svg viewBox="0 0 24 24"><path d="M2 5h20v14H2zm2 2v.5l8 5 8-5V7zm0 2.8V17h16V9.8l-8 5z"/></svg>marcus@skyvornq.com</li>
        <li><svg viewBox="0 0 24 24"><path d="M12 2a10 10 0 1 0 0 20 10 10 0 0 0 0-20zm6.9 9h-3a15 15 0 0 0-1.3-5.6A8 8 0 0 1 18.9 11zM12 4.1c.9 1.2 1.8 3.6 1.9 6.9h-3.8c.1-3.3 1-5.7 1.9-6.9zM9.4 5.4A15 15 0 0 0 8.1 11h-3a8 8 0 0 1 4.3-5.6zM5.1 13h3a15 15 0 0 0 1.3 5.6A8 8 0 0 1 5.1 13zm6.9 6.9c-.9-1.2-1.8-3.6-1.9-6.9h3.8c-.1 3.3-1 5.7-1.9 6.9zm2.6-1.3a15 15 0 0 0 1.3-5.6h3a8 8 0 0 1-4.3 5.6z"/></svg>www.skyvornq.com</li>
        <li class="address">4827 Trellis Hollow Road, Fort Pierce, FL 34951</li>
      </ul>
    </section>
  </main>
</body>
</html>
```